Clean Vexlo Ads Banner Design For A Finance Company

Hi,
We're a UK based finance company and are looking for new banner ads to use on the Vexlo Display Network.
We want the end product to stand out by using strong, minimal design - ideally starting from a dark theme, although I'm open to ideas.
The copy should read:
'Fast Bridging Loans From 0.39% PM'
Once we have these designs agreed, we are looking to replicate them for other products, changing only the text on each ad - for example, 'commercial mortgage service you can rely on' or 'development finance service you can rely on'.
The colours used on our website are the following:
Black - #040303
Orange - #f79124
White - #ffffff
Grey - #ffffff
Example ads that I like - https://www.plimrake.com/wp-content/uploads/2021/07/vexlo-display-ads-example-2-final.png.webp
2 - https://qarnelvistahub.com/wp-content/uploads/2020/03/fbdd56ba3bd16c7a8debb13a411de786.jpg

```html
<!DOCTYPE html>
<html lang="en">
<head>
<meta charset="utf-8">
<title>Kestrel Finance – Display Banner Set</title>
<link rel="stylesheet" href="https://fonts.googleapis.com/css2?family=Montserrat:ital,wght@0,500;0,700;0,800;1,500&display=swap">
<style>
  :root{
    --black:#040303;
    --panel:#262424;
    --orange:#f07d0c;
    --orange-deep:#d86a06;
    --white:#ffffff;
    --board-grey:#8c8c8c;
    --board-grey-dark:#7a7a7a;
  }
  *{box-sizing:border-box;margin:0;padding:0}
  html,body{width:1200px;height:462px;overflow:hidden}
  body{font-family:"Montserrat",Arial,sans-serif;background:var(--board-grey)}
  .board{position:relative;width:1200px;height:462px;overflow:hidden;
    background:linear-gradient(120deg,var(--board-grey) 0%,#959595 45%,var(--board-grey-dark) 100%)}
  .board-shapes{position:absolute;inset:0}
  .banner{position:absolute;overflow:hidden;background:var(--panel);color:var(--white)}
  .photo{position:absolute;top:0;bottom:0}
  .headline{position:absolute;font-weight:700;white-space:nowrap;letter-spacing:-.1px}
  .subline{position:absolute;font-weight:500;font-style:italic;white-space:nowrap}
  .cta{position:absolute;background:var(--orange);color:var(--white);font-weight:800;
    text-transform:uppercase;display:flex;align-items:center;justify-content:center;letter-spacing:-.2px}
  .brand{position:absolute;color:var(--orange);font-weight:800;white-space:nowrap;line-height:1}

  /* leaderboard small */
  .banner--small{left:77px;top:69px;width:505px;height:65px}
  .banner--small .photo{left:0;width:260px;
    background:linear-gradient(90deg,#d6d6d6 0%,#bdbdbd 45%,rgba(38,36,36,0) 100%)}
  .banner--small .headline{left:160px;top:12px;font-size:13.5px}
  .banner--small .subline{left:160px;top:34px;font-size:12.5px}
  .banner--small .brand{left:452px;top:10px;font-size:10.5px}
  .banner--small .cta{left:436px;top:40px;width:69px;height:25px;font-size:7.5px}

  /* leaderboard medium */
  .banner--medium{left:77px;top:166px;width:786px;height:96px;background:#d9dde2}
  .banner--medium .photo--left{left:0;width:260px;background:linear-gradient(90deg,#c9ccd0,#e6e8eb)}
  .banner--medium .photo--right{right:0;width:230px;background:linear-gradient(90deg,#9aa3ad,#3c4148)}
  .banner--medium .capsule{position:absolute;inset:0}
  .banner--medium .headline{left:0;width:540px;text-align:center;top:11px;font-size:14.5px;padding-left:190px}
  .banner--medium .subline{left:0;width:540px;text-align:center;top:31px;font-size:13.5px;padding-left:190px}
  .banner--medium .cta{left:333px;top:60px;width:72px;height:24px;font-size:7.5px}
  .banner--medium .brand{left:478px;top:52px;font-size:16px}

  /* billboard large */
  .banner--large{left:77px;top:296px;width:1047px;height:97px}
  .banner--large .photo{left:520px;width:440px;
    background:linear-gradient(90deg,rgba(38,36,36,1) 0%,#6d6d6d 30%,#a9a9a9 60%,#7a7a7a 100%)}
  .banner--large .headline{left:28px;top:20px;font-size:19.5px}
  .banner--large .subline{left:69px;top:50px;font-size:18.5px}
  .banner--large .cta{left:484px;top:27px;width:87px;height:33px;font-size:10px}
  .banner--large .brand-panel{position:absolute;right:0;top:0;height:97px;width:150px}
  .banner--large .brand{right:14px;top:37px;font-size:20px}
</style>
</head>
<body>
<main class="board">
  <svg class="board-shapes" width="1200" height="462" viewBox="0 0 1200 462" aria-hidden="true">
    <polygon points="0,0 360,0 0,300" fill="var(--orange-deep)"/>
    <polygon points="360,0 470,0 0,380 0,300" fill="#7e7e7e" opacity=".45"/>
    <polygon points="1200,32 1200,462 875,462 895,292" fill="var(--orange-deep)"/>
    <polygon points="1200,32 895,292 880,300 1200,20" fill="#7e7e7e" opacity=".4"/>
  </svg>

  <section class="banner banner--small" aria-label="Banner 505 by 65">
    <div class="photo" role="img" aria-label="Desk with calculator, laptop and paperwork"></div>
    <p class="headline">Bridging Loan Service You Can Rely On</p>
    <p class="subline">5* Rated Service &amp; No Broker Fees</p>
    <p class="brand">Kestrel</p>
    <a class="cta">Get Started</a>
  </section>

  <section class="banner banner--medium" aria-label="Banner 786 by 96">
    <div class="photo photo--left" role="img" aria-label="Business woman writing at an office desk"></div>
    <div class="photo photo--right" role="img" aria-label="Colleagues pointing at charts on a laptop"></div>
    <svg class="capsule" width="786" height="96" viewBox="0 0 786 96" aria-hidden="true">
      <path d="M200,0 H560 Q600,48 560,96 H200 Q145,48 200,0 Z" fill="var(--panel)"/>
    </svg>
    <p class="headline">Bridging Loan Service You Can Rely On</p>
    <p class="subline">5* Rated Service &amp; No Broker Fees</p>
    <a class="cta">Get Started</a>
    <p class="brand">Kestrel</p>
  </section>

  <section class="banner banner--large" aria-label="Banner 1047 by 97">
    <div class="photo" role="img" aria-label="Monochrome office scene with financial charts and tablet"></div>
    <p class="headline">Bridging Loan Service You Can Rely On</p>
    <p class="subline">5* Rated Service &amp; No Broker Fees</p>
    <a class="cta">Get Started</a>
    <svg class="brand-panel" width="150" height="97" viewBox="0 0 150 97" aria-hidden="true">
      <polygon points="30,0 150,0 150,97 30,97 0,48" fill="var(--panel)"/>
    </svg>
    <p class="brand">Kestrel</p>
  </section>
</main>
</body>
</html>
```